Need a design package for hair towels wrap

We need package design for hair towel wrap ( 3 pack) brand name is The Kovira. We are looking for simple, contemporary and unique design, color palette 2-3 colors. Paper Box size is 9*8*3 inches with PVC window.Actual picture of the product won't be on the package.Attached Brand Logo and description for the package. Barcode needed to be included on the design package.It will be provided later. Attached sample of the box from manufacturer, and instruction for towel wrap which idea I like, if you could make something similar to it, would be great.

Target Market(s)

Brellmart

Industry/Entity Type

Hair

Colors
848484
f5f5f5
faa54b
333333

Requirements
Must have
• Clean, contemporary design.

```html
<!DOCTYPE html>
<html lang="en">
<head>
<meta charset="utf-8">
<title>The Kovira – Microfiber Hair Towel Wrap Box</title>
<link rel="stylesheet" href="https://fonts.googleapis.com/css2?family=Lato:wght@300;400;700;900&display=swap">
<style>
  :root {
    --stage: #e9e9e9;
    --charcoal: #2b2b2b;
    --charcoal-deep: #232323;
    --side: #262626;
    --gold: #faa54b;
    --gold-line: #c98a45;
    --towel-light: #f5f5f5;
    --towel-mid: #c9c9c6;
    --grey: #848484;
    --ink-light: #f5f5f5;
  }
  * { box-sizing: border-box; margin: 0; padding: 0; }
  html, body { width: 1200px; height: 900px; overflow: hidden; }
  body {
    background: var(--stage);
    font-family: "Lato", sans-serif;
    position: relative;
  }
  .package {
    position: absolute;
    left: 200px; top: 183px;
    width: 800px; height: 534px;
    display: flex;
  }
  .box-side {
    width: 200px; height: 100%;
    background: var(--side);
    color: var(--ink-light);
    padding: 34px 22px 24px;
    display: flex;
    flex-direction: column;
    border-right: 1px solid #1a1a1a;
  }
  .feature-list { list-style: none; }
  .feature-list li {
    position: relative;
    padding-left: 16px;
    margin-bottom: 18px;
    font-size: 12px;
    line-height: 16px;
    font-weight: 400;
  }
  .feature-list li::before {
    content: "";
    position: absolute;
    left: 0; top: 5px;
    width: 6px; height: 6px;
    border-radius: 50%;
    background: var(--gold);
  }
  .care-note {
    margin-top: auto;
    font-size: 10px;
    color: var(--grey);
    letter-spacing: .3px;
  }
  .box-front {
    position: relative;
    width: 600px; height: 100%;
    background: var(--charcoal);
    overflow: hidden;
  }
  .rose-pattern {
    position: absolute; inset: 0;
    background:
      radial-gradient(circle at 14% 14%, rgba(201,138,69,.42), transparent 22%),
      radial-gradient(circle at 45% 8%, rgba(201,138,69,.32), transparent 16%),
      radial-gradient(circle at 86% 16%, rgba(201,138,69,.42), transparent 22%),
      radial-gradient(circle at 9% 52%, rgba(201,138,69,.38), transparent 20%),
      radial-gradient(circle at 92% 50%, rgba(201,138,69,.38), transparent 20%),
      radial-gradient(circle at 12% 84%, rgba(201,138,69,.36), transparent 20%),
      radial-gradient(circle at 88% 86%, rgba(201,138,69,.36), transparent 20%),
      radial-gradient(circle at 30% 95%, rgba(201,138,69,.34), transparent 18%),
      radial-gradient(circle at 62% 95%, rgba(201,138,69,.34), transparent 16%),
      var(--charcoal);
  }
  .window {
    position: absolute;
    left: 148px; top: 96px;
    width: 304px; height: 304px;
    border-radius: 50%;
    border: 5px solid var(--gold-line);
    overflow: hidden;
  }
  .window .towel {
    position: absolute; inset: 0;
    background: linear-gradient(90deg, var(--towel-mid), var(--towel-light) 40%, var(--towel-mid) 75%, var(--towel-light));
  }
  .brand {
    position: absolute;
    left: 0; right: 0; top: 26px;
    text-align: center;
  }
  .brand-mark {
    display: block;
    width: 28px; height: 28px;
    margin: 0 auto 10px;
    background: var(--gold);
  }
  .brand-name {
    font-weight: 900;
    font-size: 20px;
    letter-spacing: 1px;
    color: var(--charcoal);
  }
  .title-band {
    position: absolute;
    left: 80px; right: 80px;
    top: 228px; height: 158px;
    background: var(--charcoal-deep);
    text-align: center;
    color: var(--ink-light);
    padding-top: 12px;
  }
  .product-title {
    font-weight: 300;
    font-size: 33px;
    line-height: 35px;
    letter-spacing: .5px;
  }
  .pack-count {
    display: flex;
    align-items: center;
    justify-content: center;
    gap: 12px;
    margin-top: 7px;
    color: var(--gold);
    font-weight: 700;
    font-size: 15px;
    letter-spacing: .5px;
  }
  .pack-count::before, .pack-count::after {
    content: "";
    width: 60px; height: 1px;
    background: var(--gold);
  }
  .tagline {
    margin-top: 6px;
    font-size: 12.5px;
    line-height: 17px;
    font-weight: 400;
  }
</style>
</head>
<body>
  <main class="package">
    <aside class="box-side">
      <ul class="feature-list">
        <li>Fits all head sizes</li>
        <li>Suitable for all hair types and lengths</li>
        <li>Absorbs water fast, dries hair quicker</li>
        <li>Less time blow drying, less heat damage</li>
        <li>Reduces frizz and split ends</li>
      </ul>
      <p class="care-note">Machine wash cold</p>
    </aside>
    <section class="box-front">
      <div class="rose-pattern" role="img" aria-label="Gold line-drawn roses and leaves scattered across a charcoal background"></div>
      <div class="window">
        <div class="towel" role="img" aria-label="Rolled light grey microfiber towels seen through the box window"></div>
        <div class="brand">
          <span class="brand-mark"></span>
          <span class="brand-name">THE KOVIRA</span>
        </div>
      </div>
      <div class="title-band">
        <h1 class="product-title">MICROFIBER HAIR<br>TOWEL WRAP</h1>
        <p class="pack-count">SET OF 3 HAIR TOWELS</p>
        <p class="tagline">The softest, ultra-absorbent,<br>light &amp; safest Towel for your beautiful hair</p>
      </div>
    </section>
  </main>
</body>
</html>
```